project - Misto Den

Dear designers, I'm Looking for an appealing new business card design to represent us for our new e-cigarette store: The MistO Den. Knowledgeable and friendly staff we aim for superior customer service with a positive atmosphere. Classic feel with modern touch is what we are aiming for . Lime green font and grey back round is the original color scheme but we are flexible and open to suggestions. I added some doodles to show you where my mind is at. address: 4827 203 St SW Edmonton, AB (inside the grand swap bazaar)web: themistoden.com email: info@themistoden.com phone : 555.214.6093 Thanks and am looking forward to seeing your creative , fresh and innovative designs.
Good luck everybody!
Gordon
Updates
lime green and charcoal grey please. thanks
Industry/Entity Type
Business
Logo Text
The MistO Den
Look and feel
Each slider illustrates characteristics of the customer's brand and the style your logo design should communicate.

```html
<!DOCTYPE html>
<html lang="en">
<head>
<meta charset="utf-8">
<title>The MistO Den – Business Card</title>
<link href="https://fonts.googleapis.com/css2?family=Quicksand:wght@500;600&display=swap" rel="stylesheet">
<style>
  :root {
    --page: #eef0f1;
    --slate: #243544;
    --slate-deep: #1f2e3b;
    --haze: #9fd2e2;
    --lime: #b5f01c;
    --mist: #9aa6ae;
    --paper: #f4f7f8;
    --rule: #6d7c88;
  }
  * { box-sizing: border-box; margin: 0; padding: 0; }
  html, body { width: 1200px; height: 1000px; overflow: hidden; }
  body {
    background: var(--page);
    font-family: "Quicksand", sans-serif;
    position: relative;
  }
  .card {
    position: absolute;
    left: 206px;
    width: 788px;
    height: 450px;
    border-radius: 4px;
    overflow: hidden;
    box-shadow: 0 10px 30px rgba(0,0,0,.18);
  }
  .card--info { top: 30px; background: var(--slate); }
  .card--brand {
    top: 520px;
    background: linear-gradient(100deg, var(--slate-deep) 0%, var(--slate) 45%, #4f7488 75%, var(--haze) 100%);
  }

  .tab {
    position: absolute;
    width: 28px;
    background: var(--lime);
    border-radius: 14px;
  }
  .tab--left { left: -14px; top: 120px; height: 160px; }
  .tab--right { right: -14px; top: 80px; height: 140px; }

  .identity { position: absolute; left: 70px; top: 232px; }
  .identity__name {
    color: var(--lime);
    font-weight: 600;
    font-size: 34px;
    line-height: 1;
    letter-spacing: -.3px;
  }
  .identity__tagline {
    color: var(--mist);
    font-weight: 500;
    font-size: 22px;
    margin-top: 6px;
  }
  .identity__address {
    color: var(--lime);
    font-weight: 500;
    font-size: 20px;
    line-height: 1.3;
    margin-top: 14px;
    font-style: normal;
  }

  .divider {
    position: absolute;
    left: 478px; top: 220px;
    width: 1px; height: 112px;
    background: var(--rule);
  }

  .contacts {
    position: absolute;
    left: 520px; top: 236px;
    list-style: none;
    color: var(--lime);
    font-weight: 500;
    font-size: 17px;
  }
  .contacts li { display: flex; align-items: center; gap: 8px; height: 26px; }
  .contacts svg { width: 22px; height: 16px; flex: none; }

  .brand-rule {
    position: absolute;
    left: 0; top: 0;
    width: 788px; height: 450px;
  }
  .brand-mark {
    position: absolute;
    right: 70px; top: 228px;
    text-align: right;
  }
  .brand-mark__name {
    color: var(--lime);
    font-weight: 600;
    font-size: 62px;
    line-height: 1;
    letter-spacing: -.5px;
  }
  .brand-mark__tagline {
    color: var(--paper);
    font-weight: 500;
    font-size: 40px;
    margin-top: 8px;
  }
</style>
</head>
<body>

<section class="card card--info" aria-label="Business card, contact side">
  <span class="tab tab--left"></span>
  <span class="tab tab--right"></span>

  <div class="identity">
    <div class="identity__name">The MistO Den</div>
    <div class="identity__tagline">e-cigarette store</div>
    <address class="identity__address">4827 203 St SW Edmonton<br>AB (inside the grand swap bazaar)</address>
  </div>

  <span class="divider"></span>

  <ul class="contacts">
    <li>
      <svg viewBox="0 0 22 16" aria-hidden="true"><circle cx="11" cy="8" r="7" fill="none" stroke="#b5f01c" stroke-width="1.5"/><path d="M4 8h14M11 1c-3 4-3 10 0 14M11 1c3 4 3 10 0 14" fill="none" stroke="#b5f01c" stroke-width="1"/></svg>
      <span>: themistoden.com</span>
    </li>
    <li>
      <svg viewBox="0 0 22 16" aria-hidden="true"><rect x="2" y="2" width="18" height="12" fill="#b5f01c"/><path d="M2 2l9 7 9-7" fill="none" stroke="#243544" stroke-width="1.5"/></svg>
      <span>: info@themistoden.com</span>
    </li>
    <li>
      <svg viewBox="0 0 22 16" aria-hidden="true"><path d="M6 1l3 3-2 2c1 2 3 4 5 5l2-2 3 3-2 3C9 15 3 9 3 3z" fill="#b5f01c"/></svg>
      <span>: 555.214.6093</span>
    </li>
  </ul>
</section>

<section class="card card--brand" aria-label="Business card, brand side">
  <svg class="brand-rule" viewBox="0 0 788 450" aria-hidden="true">
    <line x1="330" y1="110" x2="250" y2="250" stroke="#6d7c88" stroke-width="1.2"/>
  </svg>
  <div class="brand-mark">
    <div class="brand-mark__name">The MistO Den</div>
    <div class="brand-mark__tagline">e-cigarette store</div>
  </div>
</section>

</body>
</html>
```